Quorbelline.io - Please redesign to make it look better from current design

We already have the current website, that you can access but we think it can improve from current version.
Quorbelline is a cryptocurrency hedge fund that allow you to participate in the hedge fund with cryptocurrency such as eth.
At current phase, we are doing an ICO, then we want to make sure that the website it looks professional, beautiful and trustable enough for investors after looking at our website.
Target Market(s)
Investors
Industry/Entity Type
Investment
Coding
Coded - Design and coding required
Number of Pages Required
1 page
Look and feel
Each slider illustrates characteristics of the customer's brand and the style your logo design should communicate.

```html
<!DOCTYPE html>
<html lang="en">
<head>
<meta charset="utf-8">
<title>Quorbelline – Digital Asset Management</title>
<link href="https://fonts.googleapis.com/css2?family=Quicksand:wght@400;500;600;700&display=swap" rel="stylesheet">
<style>
:root{
  --navy:#1c2a78;
  --ink:#222b45;
  --text:#3a3f4f;
  --muted:#6b7080;
  --sky:#35a3d6;
  --pale:#d4e8f5;
  --band:#f8f9fb;
  --line:#d9dce3;
  --white:#ffffff;
}
*{box-sizing:border-box;margin:0;padding:0}
html,body{width:1200px;height:3186px;overflow:hidden}
body{font-family:"Quicksand",sans-serif;color:var(--text);background:var(--white);position:relative}
section,header,footer{position:absolute;left:0;width:1200px}
.btn{position:absolute;display:flex;align-items:center;justify-content:center;border-radius:30px;font-weight:700;font-size:15px;letter-spacing:.5px;background:var(--sky);color:var(--white)}
.btn--ghost{background:transparent;border:1.5px solid var(--line);color:var(--muted);font-weight:500;font-size:12px}
.section-title{position:absolute;left:0;width:1200px;text-align:center;color:var(--navy);font-weight:700;font-size:19px;letter-spacing:1.5px}

/* header */
.site-header{top:0;height:121px;background:var(--white)}
.brand{position:absolute;display:flex;align-items:center;gap:10px;color:var(--navy);font-weight:700;font-size:20px}
.brand__dot{width:30px;height:30px;border-radius:50%;background:var(--navy)}
.nav{position:absolute;top:52px;left:575px;font-size:15px;font-weight:500;color:var(--ink)}
.nav a{color:inherit;text-decoration:none;position:absolute;white-space:nowrap}

/* hero */
.hero{top:121px;height:519px;background:linear-gradient(100deg,#2d4ba8 0%,#3a5bbf 45%,#27418f 100%)}
.hero__title{position:absolute;top:225px;width:1200px;text-align:center;color:var(--white);font-size:50px;font-weight:600;letter-spacing:2px}
.hero__sub{position:absolute;top:298px;width:1200px;text-align:center;color:#e3e9ff;font-size:19px;letter-spacing:1.5px}

/* welcome */
.welcome{top:640px;height:507px}
.divider{position:absolute;left:550px;top:128px;width:100px;height:2px;background:#e4e6ea}
.welcome__copy{position:absolute;left:180px;width:840px;text-align:center;font-size:14.5px;line-height:24px;color:var(--text)}

/* team */
.team{top:1147px;height:620px;background:var(--band)}
.member{position:absolute;top:132px;width:250px;height:437px;border-radius:16px;text-align:center}
.member--active{background:var(--white);box-shadow:0 8px 24px rgba(30,40,90,.12)}
.member__photo{position:absolute;left:51px;top:38px;width:148px;height:148px;border-radius:50%}
.member__name{position:absolute;top:202px;width:100%;font-weight:700;font-size:14px;color:var(--ink)}
.member--active .member__name{color:var(--navy)}
.member__role{position:absolute;top:232px;width:100%;font-size:11px;color:var(--muted)}
.member__bio{position:absolute;top:272px;left:16px;width:218px;font-size:11px;line-height:19px;color:var(--text)}
.member .btn{left:72px;top:361px;width:106px;height:32px;font-size:11px}

/* process */
.process{top:1767px;height:733px}
.step__title{position:absolute;color:var(--navy);font-weight:700;font-size:14px;letter-spacing:1px}
.step__text{position:absolute;font-size:10.5px;line-height:16px;color:var(--text)}
.step__art{position:absolute;border-radius:50%;background:var(--pale)}
.dist-list{position:absolute;list-style:none;font-size:11px;line-height:22px;color:var(--text)}
.remainder{position:absolute;font-weight:700;font-size:14px;color:var(--ink)}
.remainder-note{position:absolute;font-size:9.5px;color:var(--text)}

/* info */
.info{top:2500px;height:357px;background:var(--band)}
.info__title{position:absolute;left:202px;top:126px;color:var(--sky);font-weight:700;font-size:17px;letter-spacing:1.2px}
.info__text{position:absolute;left:204px;top:170px;width:420px;font-size:15px;line-height:27px;color:var(--ink)}
.whitepaper{position:absolute;left:697px;top:87px;width:153px;height:238px;background:linear-gradient(135deg,#1a7cd0,#0d4ea6);box-shadow:6px 6px 0 #b9c2cf}

/* footer */
.site-footer{top:2857px;height:270px;background:var(--white)}
.foot-col{position:absolute;top:58px}
.foot-col h4{color:var(--navy);font-size:14px;font-weight:700;margin-bottom:14px}
.foot-col li{list-style:none;font-size:14px;line-height:22.5px;color:var(--ink)}
.foot-col address{font-style:normal;font-size:14px;line-height:22.5px;color:var(--ink)}
.copyright{top:3127px;height:59px;background:var(--band);display:flex;align-items:center;justify-content:center;font-size:14px;color:var(--ink)}
</style>
</head>
<body>

<header class="site-header">
  <div class="brand" style="left:187px;top:44px"><span class="brand__dot"></span>Quorbelline</div>
  <nav class="nav">
    <a style="left:0">Home</a>
    <a style="left:85px">About Us</a>
    <a style="left:186px">Services</a>
    <a style="left:280px">Process</a>
    <a style="left:363px">Contact Us</a>
  </nav>
</header>

<section class="hero" role="img" aria-label="Blue-toned photo of stacked coins in front of a city skyline">
  <h1 class="hero__title">Quorbelline</h1>
  <p class="hero__sub">Digital Asset Management</p>
  <span class="btn" style="left:501px;top:350px;width:189px;height:43px">Learn More</span>
</section>

<section class="welcome">
  <h2 class="section-title" style="top:86px">WELCOME TO QUORBELLINE</h2>
  <div class="divider"></div>
  <p class="welcome__copy" style="top:172px">Quorbelline process and manages on hedge fund strategy models which invests in a diversified portfolio of blockchain tokens. Blockchain tokens are emerging which add a monetary incentive layer to p2p protocols and facilitate equity crowdfunding that anyone in the world can participate in.</p>
  <p class="welcome__copy" style="top:262px">This means open source software developers can monetize their networks at the protocol level and users of the network are the equity owners of the network. For this conditions, returns will go to holders of the tokens.</p>
  <span class="btn" style="left:501px;top:346px;width:189px;height:44px">Learn More</span>
</section>

<section class="team">
  <h2 class="section-title" style="top:54px">EXECUTIVE TEAM</h2>
  <article class="member member--active" style="left:202px">
    <div class="member__photo" role="img" aria-label="Portrait of Nattapol Keerawin" style="background:linear-gradient(160deg,#6b5a4e,#2f2a2c)"></div>
    <h3 class="member__name">Nattapol Keerawin</h3>
    <p class="member__role">Director</p>
    <p class="member__bio">As a hedge fund manager, Keerawin is the Chief Executive Officer of Ferngate Capital LLC, an investment manager...</p>
    <span class="btn">Read More</span>
  </article>
  <article class="member" style="left:474px">
    <div class="member__photo" role="img" aria-label="Portrait of Sakda Wongrit" style="background:linear-gradient(160deg,#c9c9c9,#5c5c5c)"></div>
    <h3 class="member__name">Sakda Wongrit</h3>
    <p class="member__role">Technical Advisor</p>
    <p class="member__bio">As a hedge fund manager, Wongrit is the Chief Executive Officer of Ferngate Capital LLC, an investment manager...</p>
    <span class="btn btn--ghost">Read More</span>
  </article>
  <article class="member" style="left:746px">
    <div class="member__photo" role="img" aria-label="Portrait of Kittisak Phromchai" style="background:linear-gradient(160deg,#9a3d22,#5a2418)"></div>
    <h3 class="member__name">Kittisak Phromchai</h3>
    <p class="member__role">Marketing Consultant</p>
    <p class="member__bio">As a hedge fund manager, Phromchai is the Chief Executive Officer of Ferngate Capital LLC, an investment manager...</p>
    <span class="btn btn--ghost">Read More</span>
  </article>
</section>

<section class="process">
  <h2 class="section-title" style="top:84px">PROCESS</h2>

  <h3 class="step__title" style="left:268px;top:196px">HEDGE FUND MODEL</h3>
  <p class="step__text" style="left:268px;top:244px;width:285px">Quorbelline run on closed-end fund (CEF) model which offers its shares to investors and utilize the fund to speculate and invest in the innovative blockchain tokens. Quorbelline will charge an upfront annual operation fee 4% of the money raised during the ICO. After that, the fund will charge a quarterly performance of 50% on the net profit made.</p>
  <div class="step__art" role="img" aria-label="Icon of a hand holding banknotes" style="left:582px;top:146px;width:232px;height:232px"></div>

  <div class="step__art" role="img" aria-label="Icon of a phone wallet with coins" style="left:257px;top:397px;width:264px;height:264px"></div>
  <h3 class="step__title" style="left:607px;top:473px">NET PROFIT DISTRIBUTION</h3>
  <ul class="dist-list" style="left:611px;top:516px">
    <li>50 % of net profit is distributed to investors</li>
    <li>0 – 5 % net profit &gt; 0% performance fee</li>
    <li>5 – 10% net profit &gt; 5% performance fee</li>
    <li>10-15 % net profit &gt; 13% performance fee</li>
    <li>&gt; 15% net profit &gt; 15% performance fee</li>
  </ul>
  <h4 class="remainder" style="left:613px;top:651px">The Remainder</h4>
  <p class="remainder-note" style="left:613px;top:676px">(50% minus performance fee, so at least 35%) is reinvested</p>
</section>

<section class="info">
  <h2 class="info__title">FOR MORE INFORMATION</h2>
  <p class="info__text">Neque porro quisquam est qui dolorem ipsum quia dolor sit amet, consectetur, adipisci velit...</p>
  <span class="btn" style="left:204px;top:244px;width:257px;height:43px">Download Whitepaper</span>
  <div class="whitepaper" role="img" aria-label="Cover of the Quorbelline whitepaper"></div>
</section>

<footer class="site-footer">
  <div class="brand" style="left:187px;top:44px"><span class="brand__dot"></span>Quorbelline</div>
  <div class="foot-col" style="left:406px">
    <h4>Quick Links</h4>
    <ul><li>Home</li><li>About Us</li><li>Services</li><li>Process</li><li>Contact Us</li></ul>
  </div>
  <div class="foot-col" style="left:593px">
    <h4>Other Links</h4>
    <ul><li>Terms Of Use</li><li>Privacy Policy</li><li>Help</li><li>Disclaimer</li></ul>
  </div>
  <div class="foot-col" style="left:805px">
    <h4>Contact Us</h4>
    <address>Suite 08-12, 9B/F,<br>East Tower, Linden Trade Centre,<br>Marlow Quay, 42,<br>Harbour Lane,<br>Westbay, Kowloon,<br>Hong Kong.</address>
  </div>
</footer>

<footer class="copyright">© 2017 Company Name &nbsp;|&nbsp; All Rights Reserved</footer>

</body>
</html>
```